Brief 1.
An Overview / Background of the Business & Services-
It is a new business being set up. Our business is to design a solution to enable Alumni of higher institutions in Nigeria apply for their academic transcript through our system. the name of our product will be Record Relay Nigeria. We need logo, site banner, advert banner and several academic images. See www.rrly-ng.example for more insight.
The Target Market / Audience you are trying to reach-
Alumni of Nigeria Universities, usually between the ages of 20-40.
Design Specifics; any preferences or ideas for Style, Colour, Imagery, etc-
Color scheme will be several shades of light blue and white. Please check www.rrly-ng.example for more insight.

Brief 2

Pantrybasket.com is an online food and grocery shop, we supply fresh food stuff and other daily essential needs on request to customers. The site is already up (www.pantrybasket.example). We need logo, site rolling banner, advert banner and several offer graphics as shown in the placeholder images in the site now.
Working women in Nigeria.
Color scheme will be several shades of light Green and White. Please check the site.

```html
<!DOCTYPE html>
<html lang="en">
<head>
<meta charset="utf-8">
<title>Pantry Basket — Fresh Food Online</title>
<link href="https://fonts.googleapis.com/css2?family=Open+Sans:wght@400;600;700;800&family=Roboto:wght@400;500;700&display=swap" rel="stylesheet">
<style>
:root{
  --green:#7dbb2e;
  --green-dark:#5e9c1c;
  --green-deep:#4f8a16;
  --green-light:#e9f4dc;
  --band:#8cc43f;
  --footer:#6aab26;
  --footer-base:#5a9620;
  --ink:#333;
  --muted:#888;
  --line:#dcdcdc;
  --price:#444;
  --white:#fff;
}
*{box-sizing:border-box;margin:0;padding:0}
html,body{width:711px;height:1200px;overflow:hidden;background:var(--white);font-family:"Open Sans",Arial,sans-serif;color:var(--ink)}
.page{position:relative;width:711px;height:1200px}
.abs{position:absolute}

/* header */
.brand{left:57px;top:24px;display:flex;align-items:center;gap:8px;font-family:"Roboto",Arial,sans-serif;font-weight:700;font-size:22px;color:var(--green)}
.brand-mark{width:22px;height:22px;background:var(--green);border-radius:3px}
.top-links{right:52px;top:6px;font-size:8px;color:var(--muted);display:flex;gap:6px}
.search{left:282px;top:40px;width:150px;height:18px;border:1px solid var(--line);border-radius:2px;font-size:8px;color:#aaa;padding:3px 6px;display:flex;justify-content:space-between;align-items:center}
.cart{right:52px;top:38px;width:58px;height:20px;background:var(--green);color:#fff;font-size:8px;border-radius:2px;display:flex;align-items:center;justify-content:center;gap:4px}

/* nav */
.nav{left:57px;top:72px;width:603px;height:20px;background:var(--band);display:flex;font-size:8.5px;font-weight:700;color:#fff}
.nav a{padding:0 12px;display:flex;align-items:center;text-decoration:none;color:#fff}
.nav a.active{background:var(--green-deep)}

/* hero */
.hero{left:57px;top:92px;width:603px;height:192px;background:linear-gradient(90deg,#f7f7f7,#eef1ec)}
.hero-visual{right:40px;top:12px;width:190px;height:172px;border-radius:50%;background:radial-gradient(circle at 45% 45%,#e2483a 0%,#c7362a 45%,#8ec64a 70%,transparent 72%)}
.hero h1{position:absolute;left:14px;top:60px;font-family:"Roboto",Arial,sans-serif;font-size:24px;font-weight:500;color:var(--green-dark)}
.hero h2{position:absolute;left:14px;top:92px;font-size:13px;font-weight:400;color:var(--green)}
.hero p{position:absolute;left:14px;top:114px;width:180px;font-size:6.5px;line-height:1.5;color:var(--muted)}
.dots{position:absolute;left:14px;top:148px;display:flex;gap:4px}
.dots i{width:5px;height:5px;border-radius:50%;background:#ccc}
.dots i:first-child{background:var(--green)}

/* sidebar */
.side-head{width:145px;height:20px;background:var(--green);color:#fff;font-size:11px;font-weight:600;padding:3px 8px}
.cat-list{left:57px;top:375px;width:145px;border:1px solid var(--line);border-top:0;padding:6px 8px;font-size:6.5px;line-height:13px;color:#555;list-style:none}
.cat-list li:before{content:"› ";color:var(--green)}
.best{left:57px;top:518px;width:145px;border:1px solid var(--line);border-top:0;padding:6px}
.best-item{display:flex;gap:6px;margin-bottom:7px}
.best-thumb{width:34px;height:30px;background:linear-gradient(135deg,#c9562f,#e3a04b)}
.best-item b{display:block;font-size:7px}
.best-item span{display:block;font-size:6.5px;color:var(--muted)}
.mini-btn{display:inline-block;margin-top:2px;background:var(--green);color:#fff;font-size:5.5px;padding:1px 5px;border-radius:2px}
.side-ad{left:57px;top:692px;width:145px;height:132px;background:linear-gradient(180deg,#2e3e5c,#b55a2a 60%,#e2b24a)}

/* main */
.tiles{left:222px;top:355px;width:438px;display:flex;gap:6px}
.tile{position:relative;flex:1;height:90px}
.tile span{position:absolute;left:0;right:0;bottom:0;height:16px;background:rgba(110,170,40,.85);color:#fff;font-size:7.5px;font-weight:600;padding:3px 6px}
.t1{background:linear-gradient(135deg,#d9c6b4,#a88d7a)}
.t2{background:linear-gradient(135deg,#d13b2a,#8ac24a 55%,#f0b33a)}
.t3{background:linear-gradient(135deg,#c58a4a,#7a4a2a)}
.section-title{left:222px;top:458px;font-family:"Roboto",Arial,sans-serif;font-size:15px;font-weight:500;color:var(--ink)}
.grid{left:222px;top:483px;width:438px;display:grid;grid-template-columns:repeat(3,1fr);column-gap:14px;row-gap:22px}
.card{height:108px}
.card-img{height:62px;border:1px solid var(--line);display:flex;align-items:center;justify-content:center}
.card-img div{width:70%;height:55%;border-radius:40%}
.fish{background:linear-gradient(90deg,#8a8f8c,#c9cdc6)}
.fish2{background:linear-gradient(90deg,#6c6f66,#a9ab9e)}
.apple{width:36%!important;height:70%!important;border-radius:50%!important;background:radial-gradient(circle at 40% 40%,#e3473a,#a82318)}
.card-foot{display:flex;justify-content:space-between;align-items:center;padding-top:6px}
.card-foot small{display:block;font-size:7px;color:var(--muted)}
.card-foot b{display:block;font-size:10px;color:var(--price);font-weight:600}
.promo{left:222px;top:745px;width:438px;height:84px;background:linear-gradient(90deg,#f3e4c8,#e58c3a 55%,#c8352a)}

/* footer */
.perks{left:0;top:872px;width:711px;height:58px;background:var(--green-light);display:flex;justify-content:center;gap:28px;align-items:center}
.perk{display:flex;gap:7px;align-items:center}
.perk b{display:block;font-size:9px;color:var(--green-deep)}
.perk span{display:block;font-size:6.5px;color:var(--muted)}
.footer{left:0;top:930px;width:711px;height:243px;background:var(--footer);color:#fff;padding:26px 57px;display:flex;gap:28px}
.col h4{font-size:8px;font-weight:700;margin-bottom:8px;letter-spacing:.3px}
.col ul{list-style:none;font-size:6px;line-height:12px;color:#e8f4d8}
.social{display:flex;gap:5px}
.social i{width:16px;height:16px;border-radius:50%;background:#fff;opacity:.9}
.pay{display:flex;gap:4px;margin-top:14px}
.pay i{width:22px;height:14px;background:#fff;border-radius:2px;opacity:.9}
.base{left:0;top:1173px;width:711px;height:27px;background:var(--footer-base);color:#d9ecc4;font-size:6px;padding:9px 57px}
</style>
</head>
<body>
<div class="page">

  <div class="abs brand"><span class="brand-mark"></span>Pantry Basket</div>
  <div class="abs top-links"><span>My Account</span>|<span>My Cart</span>|<span>Shop Here</span>|<span>Contact</span></div>
  <div class="abs search"><span>Search here...</span>
    <svg width="9" height="9" viewBox="0 0 10 10"><circle cx="4" cy="4" r="3" fill="none" stroke="#999" stroke-width="1.2"/><line x1="6.3" y1="6.3" x2="9" y2="9" stroke="#999" stroke-width="1.2"/></svg>
  </div>
  <div class="abs cart">
    <svg width="10" height="9" viewBox="0 0 10 9"><path d="M0 1h2l1.2 5h5L9.5 2.5H3" fill="none" stroke="#fff" stroke-width="1"/><circle cx="4" cy="8" r=".8" fill="#fff"/><circle cx="7.5" cy="8" r=".8" fill="#fff"/></svg>0 items</div>

  <nav class="abs nav">
    <a class="active">HOME</a><a>HEALTH &amp; WELLNESS</a><a>FRUITS &amp; VEGS</a><a>POULTRY, MEAT &amp; FISH</a><a>FOOD STUFFS</a><a>RECIPES</a>
  </nav>

  <section class="abs hero">
    <div class="abs hero-visual" role="img" aria-label="Fresh red apple with sliced fruit and green leaves"></div>
    <h1>Premmium Quality</h1>
    <h2>Suspendisse vulputate aliquam</h2>
    <p>Fresh produce picked daily and delivered straight to your kitchen door across the city.</p>
    <div class="dots"><i></i><i></i><i></i></div>
  </section>

  <div class="abs side-head" style="left:57px;top:355px">Categories</div>
  <ul class="abs cat-list">
    <li>HEALTH &amp; WELLNESS</li><li>FRUITS &amp; VEGS</li><li>POULTRY, MEAT &amp; FISH</li><li>FOOD STUFFS</li><li>RECIPES</li><li>OTHERS</li>
  </ul>

  <div class="abs side-head" style="left:57px;top:498px">Best Sellings</div>
  <div class="abs best">
    <div class="best-item"><div class="best-thumb" role="img" aria-label="Grilled chicken dish"></div><div><b>Product Name</b><span>$1,400</span><span class="mini-btn">ADD TO CART</span></div></div>
    <div class="best-item"><div class="best-thumb" role="img" aria-label="Pepper stew"></div><div><b>Product Name</b><span>$1,400</span><span class="mini-btn">ADD TO CART</span></div></div>
    <div class="best-item"><div class="best-thumb" role="img" aria-label="Fried rice plate"></div><div><b>Product Name</b><span>$1,400</span><span class="mini-btn">ADD TO CART</span></div></div>
    <div class="best-item"><div class="best-thumb" role="img" aria-label="Roasted meat platter"></div><div><b>Product Name</b><span>$1,400</span><span class="mini-btn">ADD TO CART</span></div></div>
  </div>
  <div class="abs side-ad" role="img" aria-label="Advert for Harbor Pines Retreats resort properties at sunset"></div>

  <div class="abs tiles">
    <div class="tile t1" role="img" aria-label="Health and wellness category"><span>Health &amp; Wellness</span></div>
    <div class="tile t2" role="img" aria-label="Fresh fruits and vegetables category"><span>Fresh Fruits &amp; Veg.</span></div>
    <div class="tile t3" role="img" aria-label="Herbals and recipes category"><span>Herbals &amp; Recipes</span></div>
  </div>

  <div class="abs section-title">Featured Products</div>
  <div class="abs grid">
    <div class="card"><div class="card-img"><div class="fish" role="img" aria-label="Whole fresh fish"></div></div><div class="card-foot"><div><small>Product Name</small><b>$255.00</b></div><svg class="bag" width="18" height="18" viewBox="0 0 18 18"><rect x="2" y="6" width="14" height="11" rx="2" fill="none" stroke="#7dbb2e" stroke-width="1.6"/><path d="M6 8V5a3 3 0 0 1 6 0v3" fill="none" stroke="#7dbb2e" stroke-width="1.6"/></svg></div></div>
    <div class="card"><div class="card-img"><div class="fish2" role="img" aria-label="Tilapia fish"></div></div><div class="card-foot"><div><small>Product Name</small><b>$255.00</b></div><svg width="18" height="18" viewBox="0 0 18 18"><rect x="2" y="6" width="14" height="11" rx="2" fill="none" stroke="#7dbb2e" stroke-width="1.6"/><path d="M6 8V5a3 3 0 0 1 6 0v3" fill="none" stroke="#7dbb2e" stroke-width="1.6"/></svg></div></div>
    <div class="card"><div class="card-img"><div class="apple" role="img" aria-label="Red apple"></div></div><div class="card-foot"><div><small>Product Name</small><b>$255.00</b></div><svg width="18" height="18" viewBox="0 0 18 18"><rect x="2" y="6" width="14" height="11" rx="2" fill="none" stroke="#7dbb2e" stroke-width="1.6"/><path d="M6 8V5a3 3 0 0 1 6 0v3" fill="none" stroke="#7dbb2e" stroke-width="1.6"/></svg></div></div>
    <div class="card"><div class="card-img"><div class="apple" role="img" aria-label="Red apple"></div></div><div class="card-foot"><div><small>Product Name</small><b>$255.00</b></div><svg width="18" height="18" viewBox="0 0 18 18"><rect x="2" y="6" width="14" height="11" rx="2" fill="none" stroke="#7dbb2e" stroke-width="1.6"/><path d="M6 8V5a3 3 0 0 1 6 0v3" fill="none" stroke="#7dbb2e" stroke-width="1.6"/></svg></div></div>
    <div class="card"><div class="card-img"><div class="fish" role="img" aria-label="Whole fresh fish"></div></div><div class="card-foot"><div><small>Product Name</small><b>$255.00</b></div><svg width="18" height="18" viewBox="0 0 18 18"><rect x="2" y="6" width="14" height="11" rx="2" fill="none" stroke="#7dbb2e" stroke-width="1.6"/><path d="M6 8V5a3 3 0 0 1 6 0v3" fill="none" stroke="#7dbb2e" stroke-width="1.6"/></svg></div></div>
    <div class="card"><div class="card-img"><div class="fish2" role="img" aria-label="Tilapia fish"></div></div><div class="card-foot"><div><small>Product Name</small><b>$255.00</b></div><svg width="18" height="18" viewBox="0 0 18 18"><rect x="2" y="6" width="14" height="11" rx="2" fill="none" stroke="#7dbb2e" stroke-width="1.6"/><path d="M6 8V5a3 3 0 0 1 6 0v3" fill="none" stroke="#7dbb2e" stroke-width="1.6"/></svg></div></div>
  </div>

  <div class="abs promo" role="img" aria-label="Advert banner for freeze-dried fruits and vegetables with a pile of dried fruit"></div>

  <section class="abs perks">
    <div class="perk"><svg width="24" height="16" viewBox="0 0 24 16"><rect x="1" y="3" width="13" height="9" fill="none" stroke="#5e9c1c" stroke-width="1.5"/><path d="M14 6h5l3 3v3h-8z" fill="none" stroke="#5e9c1c" stroke-width="1.5"/><circle cx="6" cy="13.5" r="1.8" fill="#5e9c1c"/><circle cx="18" cy="13.5" r="1.8" fill="#5e9c1c"/></svg><div><b>FREE SHIPPING</b><span>On Order over $30 after today</span></div></div>
    <div class="perk"><svg width="16" height="16" viewBox="0 0 16 16"><path d="M3 1l3 3-2 2c1 2 3 4 5 5l2-2 3 3-2 3C6 14 2 10 1 3z" fill="#5e9c1c"/></svg><div><b>GIVE US CALL NOW</b><span>1-800-555-0142 / 1-800-555-0177</span></div></div>
    <div class="perk"><svg width="24" height="16" viewBox="0 0 24 16"><rect x="1" y="3" width="13" height="9" fill="none" stroke="#5e9c1c" stroke-width="1.5"/><path d="M14 6h5l3 3v3h-8z" fill="none" stroke="#5e9c1c" stroke-width="1.5"/><circle cx="6" cy="13.5" r="1.8" fill="#5e9c1c"/><circle cx="18" cy="13.5" r="1.8" fill="#5e9c1c"/></svg><div><b>FREE DELIVERY &amp; 10% DISCOUNT</b><span>On every Registered Users</span></div></div>
  </section>

  <footer class="abs footer">
    <div class="col"><h4>COMPANY</h4><ul><li>ABOUT US</li><li>CAREERS</li><li>PRESS ROOM</li><li>BLOG</li><li>SITEMAP</li></ul></div>
    <div class="col"><h4>FEATURES PRODUCTS</h4><ul><li>FRESH HERBS DAILY</li><li>ORGANIC VEGETABLES</li><li>LOCAL FARM POULTRY</li><li>WHOLE GRAIN STAPLES</li><li>SEASONAL FRUIT BOXES</li></ul></div>
    <div class="col"><h4>RESOURCES</h4><ul><li>ORDER &amp; DELIVERY POLICY</li><li>INTERNATIONAL DELIVERY</li><li>CONTACT US</li><li>SUPPORT</li><li>TESTIMONIALS</li></ul></div>
    <div class="col"><h4>SUPPORT</h4><ul><li>HELP CENTRE FAQ</li><li>RETURNS POLICY</li><li>PAYMENT OPTIONS</li><li>TRACK YOUR ORDER</li><li>PRIVACY NOTICE</li></ul></div>
    <div class="col"><h4>GET IN TOUCH</h4><div class="social"><i></i><i></i><i></i><i></i></div><div class="pay"><i></i><i></i><i></i><i></i></div></div>
  </footer>
  <div class="abs base">© 2016 Pantrybasket.com. All rights reserved. Terms of Use</div>

</div>
</body>
</html>
```